3 in 1 website - Property Lens Works + Keepsake Harbor LLC + Marla's Game Shots

Help me simplify and organize my business life. I am a sports photographer (action, individual and teams), real estate photographer (stills and drones) and I transfer videos and photos to jump drives, along with photo restoration, etc. Currently, I have a functioning website for the transfer/restoration business at KeepsakeHarborLLC.example which was recently created and I like it. I have received several really good ideas for the Real Estate Photography portion! I don't have anything started for the Sports Pics. My vision possibly includes a main/home page giving people the option to choose real estate, sports or transfer/restoration. I just want them combined into one site....somehow to better organize my businesses and give me ONE place to keep to updated and check for communication. I just updated the brief again and added logo files for my "parent" company called "Keepsake Harbor". I prefer this logo at the top of the main/home page, please. I previously uploaded the logo for Property Lens Works which would be used with the real estate portion of my business. At this point, I don't have a logo for the sports photography portion.

Target Market(s)

Real Estate Agents and Brokers; Sports team, parents and boosters; Community members typically 40+ years old

Industry/Entity Type

Real Estate Photography; Local sports teams; Community members 40+ years old

Coding

Coded - Design and coding required

Number of Pages Required

3 page

Requirements
Must have
• At least one page for each area: real estate, sports, digital transfers. The real estate will need to connect to an account I have with QLN for checkout options. The sports page(s) will need to connect to a 3rd party service, also. The digital transfers, photo restorations, etc. would just need a way for them to request service.
Nice to have
• I currently have a website at KeepsakeHarborLLC.example for the digital transfer/photo restoration part of my business. I like this website but want it integrated with one main site for all 3 businesses.

```html
<!DOCTYPE html>
<html lang="en">
<head>
<meta charset="utf-8">
<title>Marla Penrose Real Estate Photographer</title>
<link rel="stylesheet" href="https://fonts.googleapis.com/css2?family=Lato:wght@400;700;900&display=swap">
<style>
:root{
  --teal:#13a396;
  --teal-dark:#0c8c80;
  --red:#e6202b;
  --ink:#141414;
  --text:#333;
  --grey-bg:#f2f2f2;
  --blue:#1565b4;
  --form-bg:#eef5fa;
  --black:#050505;
}
*{box-sizing:border-box;margin:0;padding:0}
html,body{width:1200px;height:3811px;overflow:hidden}
body{position:relative;font-family:'Lato',sans-serif;color:var(--text);background:#fff}
.abs{position:absolute}
a{color:inherit;text-decoration:none}

/* header */
.topbar{left:392px;top:0;width:808px;height:55px;background:var(--teal);clip-path:polygon(0 0,100% 0,100% 100%,36px 100%);color:#fff;font-size:15px;font-weight:700}
.topbar .item{position:absolute;top:19px;display:flex;align-items:center;gap:10px}
.topbar .sep{position:absolute;top:20px;width:1px;height:15px;background:rgba(255,255,255,.6)}
.social-sq{position:absolute;top:16px;width:25px;height:25px;border:1.5px solid #fff;border-radius:2px}
.brand{left:111px;top:34px;font-size:29px;font-weight:900;color:var(--red);letter-spacing:.3px}
.nav{top:82px;left:409px;display:flex;font-size:14px;font-weight:700;color:var(--ink)}
.nav a{position:absolute;white-space:nowrap}
.nav a.active{color:var(--teal);text-decoration:underline}
.btn{display:flex;align-items:center;justify-content:center;color:#fff;font-weight:700;font-size:15px;position:absolute;z-index:2;isolation:isolate}
.btn::before{content:"";position:absolute;inset:0;background:var(--teal);transform:skewX(-12deg);box-shadow:4px 3px 0 #d7d7d7;z-index:-1}
.btn span{position:relative}
.btn.red::before{background:var(--red);box-shadow:5px 3px 0 #fff}
.btn.contact{left:1001px;top:67px;width:126px;height:43px;font-size:14px}

/* hero */
.hero-svg{left:0;top:124px}
.hero-text{left:110px;color:#fff}
.hero-kicker{top:214px;font-size:26px;font-weight:700}
.hero-title{top:250px;font-size:42px;font-weight:900;line-height:51px}
.hero-copy{top:362px;font-size:15px;line-height:26px;width:560px}
.hero-photo{left:742px;top:198px;width:352px;height:272px;background:linear-gradient(135deg,#c9c3b9,#f3f1ee 45%,#8d8a85);border:6px solid #fff;border-radius:8px;transform:rotate(2deg);box-shadow:12px 12px 0 var(--red)}
.dot{top:612px;width:10px;height:10px;border-radius:50%;background:#fff}

/* section bits */
.mark{width:22px;height:22px;border-radius:50%;background:var(--blue)}
.kicker{font-size:31px;font-weight:900;color:var(--red)}
.heading{font-size:31px;font-weight:900;color:var(--ink)}
.copy{font-size:15px;line-height:26px;color:var(--text)}

.about-houses{left:0;top:873px;width:1200px;height:355px;background:linear-gradient(180deg,#fff 0%,#f4e3c9 35%,#c9b79b 60%,#6d7a6c 100%)}
.about-fade{left:0;top:873px;width:1200px;height:200px;background:linear-gradient(180deg,#fff 0%,rgba(255,255,255,.85) 60%,rgba(255,255,255,0) 100%)}

.band-grey{left:0;width:1200px;background:var(--grey-bg)}
.frame{border:3px solid var(--teal)}
.frame.blue{border-color:var(--blue)}
.photo{background:linear-gradient(135deg,#e7e5e2,#b8b2aa 55%,#5d5a57)}

/* contact */
.addr-label{font-size:25px;font-weight:700;color:var(--ink)}
.info-circle{width:63px;height:63px;border-radius:50%;background:var(--teal);display:flex;align-items:center;justify-content:center}
.info-title{font-size:18px;font-weight:700;color:var(--ink)}
.info-val{font-size:16px;color:#777;line-height:22px}
.form-box{left:553px;top:2967px;width:536px;height:397px;background:var(--form-bg)}
.field{position:absolute;background:#fff;box-shadow:0 2px 6px rgba(0,0,0,.06);font-size:15px;color:#666;padding:14px 17px}

/* footer */
.footer-brand{left:111px;top:3654px;font-size:32px;font-weight:900;color:var(--red)}
.fnav a{position:absolute;top:3608px;color:#fff;font-size:14px;white-space:nowrap}
.fline{color:#fff;font-size:12.5px}
.fsocial{top:3722px;width:24px;height:24px;border-radius:50%;background:var(--teal)}
.bottom-strip{left:0;top:3793px;width:1200px;height:18px;background:var(--teal)}
</style>
</head>
<body>

<header>
  <div class="abs topbar">
    <div class="item" style="left:20px">
      <svg width="18" height="18" viewBox="0 0 24 24" fill="#fff"><path d="M6.6 10.8a15.1 15.1 0 0 0 6.6 6.6l2.2-2.2c.3-.3.7-.4 1-.2 1.1.4 2.3.6 3.6.6.6 0 1 .4 1 1V20c0 .6-.4 1-1 1A17 17 0 0 1 3 4c0-.6.4-1 1-1h3.5c.6 0 1 .4 1 1 0 1.2.2 2.4.6 3.6.1.3 0 .7-.2 1z"/></svg>
    </div>
    <div class="sep" style="left:55px"></div>
    <div class="item" style="left:76px">Call:+1 555 010 0188</div>
    <div class="item" style="left:254px">
      <svg width="17" height="13" viewBox="0 0 24 18" fill="#fff"><path d="M1 1h22v16H1z"/><path d="M1 1l11 8 11-8" stroke="var(--teal)" stroke-width="2" fill="none"/></svg>
    </div>
    <div class="sep" style="left:290px"></div>
    <div class="item" style="left:312px">Mail:info@marlapenrose.example</div>
    <div class="item" style="left:553px">
      <svg width="24" height="22" viewBox="0 0 24 22" fill="#fff"><path d="M0 1h4l3 12h13l3-9H6" stroke="#fff" stroke-width="2" fill="none"/><circle cx="9" cy="18" r="2"/><circle cx="18" cy="18" r="2"/><circle cx="21" cy="2" r="4" fill="var(--red)"/></svg>
    </div>
    <div class="social-sq" style="left:605px"></div>
    <div class="social-sq" style="left:651px"></div>
    <div class="social-sq" style="left:697px"></div>
  </div>
  <div class="abs brand">MARLA PENROSE</div>
  <nav class="abs nav">
    <a class="active" style="left:0">HOME</a>
    <a style="left:87px">ABOUT US</a>
    <a style="left:195px">REAL ESTATE</a>
    <a style="left:326px">SPORTS</a>
    <a style="left:422px">DIGITAL TRANSFERS</a>
  </nav>
  <a class="btn contact"><span>CONTACT US</span></a>
</header>

<section>
  <svg class="abs hero-svg" width="1200" height="600" viewBox="0 124 1200 600" role="img" aria-label="Teal backdrop of faded scattered property photographs">
    <defs>
      <linearGradient id="heroGrad" x1="0" y1="0" x2="1" y2="1">
        <stop offset="0" stop-color="#16a89b"/>
        <stop offset="1" stop-color="#0e9185"/>
      </linearGradient>
    </defs>
    <polygon points="0,124 1200,124 1200,620 1088,570 600,690 111,570 0,620" fill="url(#heroGrad)"/>
    <polygon points="0,620 111,570 600,690 1088,570 1200,620 1200,652 1088,596 600,714 111,596 0,652" fill="var(--red)"/>
  </svg>
  <div class="abs hero-text hero-kicker">WELCOME TO</div>
  <div class="abs hero-text hero-title">MARLA PENROSE<br>REAL ESTATE PHOTOGRAPHY</div>
  <p class="abs hero-text hero-copy">Itaque earum rerum hic tenetur a sapiente delectus, ut aut reiciendis voluptatibus maiores alias consequatur aut perferendis doloribus asperiores repellat.</p>
  <a class="btn red" style="left:116px;top:434px;width:248px;height:53px;font-size:15px"><span>SCHEDULE APPOINTMENTS</span></a>
  <div class="abs hero-photo" role="img" aria-label="Photographer shooting a bright modern kitchen interior"></div>
  <div class="abs dot" style="left:572px"></div>
  <div class="abs dot" style="left:595px;background:var(--red)"></div>
  <div class="abs dot" style="left:617px"></div>
</section>

<section>
  <div class="abs about-houses" role="img" aria-label="Row of suburban houses at sunset"></div>
  <div class="abs about-fade"></div>
  <div class="abs mark" style="left:589px;top:772px"></div>
  <div class="abs kicker" style="left:0;width:1200px;text-align:center;top:816px">ABOUT</div>
  <div class="abs heading" style="left:0;width:1200px;text-align:center;top:858px">MARLA PENROSE REAL ESTATE PHOTOGRAPHER</div>
  <p class="abs copy" style="left:160px;width:880px;text-align:center;top:905px">Nam libero tempore, cum soluta nobis est eligendi optio cumque nihil impedit quo minus id quod maxime placeat facere possimus, omnis voluptas assumenda est, omnis dolor repellendus.</p>
  <p class="abs copy" style="left:160px;width:880px;text-align:center;top:982px">Temporibus autem quibusdam et aut officiis debitis aut rerum necesstates repudiandae sint et molestiae non recusandae. Itaque earum rerum hic tenetur a sapiente delectus, ut aut reiciendis voluptatibus maioresrerum necessitatibus saepe eveniet&nbsp; alias consequatur aut perferendis doloribus asperiores repellat.</p>
  <a class="btn" style="left:530px;top:1074px;width:141px;height:45px"><span>READ MORE</span></a>
</section>

<section>
  <div class="abs band-grey" style="top:1228px;height:481px"></div>
  <div class="abs frame" style="left:599px;top:1261px;width:564px;height:407px"></div>
  <div class="abs photo" style="left:636px;top:1296px;width:564px;height:409px" role="img" aria-label="Hands holding printed interior photos beside a laptop"></div>
  <div class="abs mark" style="left:148px;top:1346px"></div>
  <div class="abs kicker" style="left:111px;top:1393px">REAL</div>
  <div class="abs heading" style="left:111px;top:1430px">ESTATE PHOTOGRAPHY</div>
  <p class="abs copy" style="left:111px;top:1474px;width:430px">Temporibus autem quibusdam et aut officiis debitis aut rerum necluptates repudiandae sint et molestiae non recusandae.</p>
  <p class="abs copy" style="left:111px;top:1551px;width:430px">Itaque earum rerum hic tenetur a sapiente delectus, ut aut doloribus asperiores repellat.</p>
  <a class="btn" style="left:117px;top:1615px;width:141px;height:44px"><span>LEARN MORE</span></a>
</section>

<section>
  <div class="abs photo" style="left:0;top:1814px;width:564px;height:409px;background:linear-gradient(135deg,#5d8a3a,#9fbe6a 45%,#c46a45 70%,#2b2b2b)" role="img" aria-label="Photographer with a long lens at a football field"></div>
  <div class="abs frame blue" style="left:37px;top:1779px;width:561px;height:407px"></div>
  <div class="abs mark" style="left:681px;top:1864px"></div>
  <div class="abs kicker" style="left:644px;top:1911px">SPORTS</div>
  <div class="abs heading" style="left:644px;top:1950px">PHOTOGRAPHY</div>
  <p class="abs copy" style="left:644px;top:1994px;width:430px">Temporibus autem quibusdam et aut officiis debitis aut rerum necluptates repudiandae sint et molestiae non recusandae.</p>
  <p class="abs copy" style="left:644px;top:2071px;width:430px">Itaque earum rerum hic tenetur a sapiente delectus, ut aut doloribus asperiores repellat.</p>
  <a class="btn" style="left:650px;top:2131px;width:141px;height:45px"><span>LEARN MORE</span></a>
</section>

<section>
  <div class="abs band-grey" style="top:2301px;height:478px"></div>
  <div class="abs frame" style="left:599px;top:2334px;width:564px;height:407px"></div>
  <div class="abs photo" style="left:636px;top:2369px;width:564px;height:409px;background:linear-gradient(135deg,#d4d8dc,#8d9298 50%,#1c1c1c)" role="img" aria-label="Vintage folding camera resting on old photographs"></div>
  <div class="abs mark" style="left:148px;top:2419px"></div>
  <div class="abs kicker" style="left:111px;top:2466px">DIGITAL</div>
  <div class="abs heading" style="left:111px;top:2503px">TRANSFERS</div>
  <p class="abs copy" style="left:111px;top:2547px;width:430px">Temporibus autem quibusdam et aut officiis debitis aut rerum necluptates repudiandae sint et molestiae non recusandae.</p>
  <p class="abs copy" style="left:111px;top:2624px;width:430px">Itaque earum rerum hic tenetur a sapiente delectus, ut aut doloribus asperiores repellat.</p>
  <a class="btn" style="left:117px;top:2688px;width:141px;height:44px"><span>LEARN MORE</span></a>
</section>

<section>
  <div class="abs mark" style="left:586px;top:2866px;width:28px;height:28px"></div>
  <div class="abs heading" style="left:0;width:1200px;text-align:center;top:2904px">GET IN <span style="color:var(--red)">TOUCH WITH</span> US</div>
  <div class="abs addr-label" style="left:110px;top:2986px">Address</div>

  <div class="abs info-circle" style="left:112px;top:3034px">
    <svg width="20" height="26" viewBox="0 0 20 26"><path d="M10 0a10 10 0 0 0-10 10c0 7 10 16 10 16s10-9 10-16A10 10 0 0 0 10 0z" fill="#fff"/><circle cx="10" cy="10" r="3.5" fill="var(--teal)"/></svg>
  </div>
  <div class="abs info-title" style="left:194px;top:3032px">LOCATION</div>
  <div class="abs info-val" style="left:192px;top:3060px">Marla Penrose Real Estate<br>Photographer. United States</div>

  <div class="abs info-circle" style="left:112px;top:3135px">
    <svg width="22" height="22" viewBox="0 0 24 24" fill="#fff"><path d="M6.6 10.8a15.1 15.1 0 0 0 6.6 6.6l2.2-2.2c.3-.3.7-.4 1-.2 1.1.4 2.3.6 3.6.6.6 0 1 .4 1 1V20c0 .6-.4 1-1 1A17 17 0 0 1 3 4c0-.6.4-1 1-1h3.5c.6 0 1 .4 1 1 0 1.2.2 2.4.6 3.6.1.3 0 .7-.2 1z"/></svg>
  </div>
  <div class="abs info-title" style="left:195px;top:3141px">PHONE NUMBER</div>
  <div class="abs info-val" style="left:195px;top:3171px">+1 555 010 0188</div>

  <div class="abs info-circle" style="left:112px;top:3232px">
    <svg width="22" height="16" viewBox="0 0 24 18"><rect x="1" y="1" width="22" height="16" fill="#fff"/><path d="M1 1l11 8 11-8" stroke="var(--teal)" stroke-width="2" fill="none"/></svg>
  </div>
  <div class="abs info-title" style="left:195px;top:3239px">EMAIL ADDRESS</div>
  <div class="abs info-val" style="left:194px;top:3267px">info@marlapenrose.example</div>

  <div class="abs form-box"></div>
  <div class="field" style="left:582px;top:3012px;width:238px;height:49px">First Name</div>
  <div class="field" style="left:829px;top:3012px;width:238px;height:49px">Your Email</div>
  <div class="field" style="left:582px;top:3074px;width:238px;height:49px">Your Phone</div>
  <div class="field" style="left:829px;top:3074px;width:238px;height:49px">Address</div>
  <div class="field" style="left:582px;top:3138px;width:485px;height:111px">Message</div>
  <a class="btn" style="left:588px;top:3277px;width:141px;height:44px"><span>SUBMIT</span></a>
  <div class="abs" style="left:1033px;top:3293px;width:95px;height:96px;background:rgba(19,163,150,.12)" role="img" aria-label="Dotted accent pattern"></div>
</section>

<footer>
  <svg class="abs" style="left:0;top:3410px" width="1200" height="383" viewBox="0 3410 1200 383">
    <polygon points="0,3471 111,3545 600,3419 1088,3545 1200,3471 1200,3793 0,3793" fill="var(--red)"/>
    <polygon points="0,3497 111,3560 600,3440 1088,3560 1200,3497 1200,3793 0,3793" fill="#fff"/>
    <polygon points="0,3510 111,3574 600,3455 1088,3574 1200,3510 1200,3793 0,3793" fill="var(--black)"/>
  </svg>
  <div class="abs footer-brand">MARLA PENROSE</div>
  <nav class="fnav">
    <a style="left:463px">HOME</a>
    <a style="left:551px">ABOUT</a>
    <a style="left:642px">REAL ESTATE</a>
    <a style="left:773px">SPORTS</a>
    <a style="left:869px">DIGITAL TRANSFERS</a>
    <a style="left:1049px">CONTACT US</a>
  </nav>
  <div class="abs fline" style="left:466px;top:3645px">&#9990;&nbsp; Phone : +1 555 010 0188 &nbsp;&nbsp;&nbsp;&nbsp;&nbsp;|&nbsp;&nbsp;&nbsp;&nbsp;&nbsp; &#9993;&nbsp; Email : info@marlapenrose.example</div>
  <div class="abs fline" style="left:463px;top:3690px;font-size:11px">Copyrights@2023.Marla Penrose Real Estate Photographer..All Rights Reserved</div>
  <div class="abs fsocial" style="left:466px"></div>
  <div class="abs fsocial" style="left:513px"></div>
  <div class="abs fsocial" style="left:561px"></div>
  <div class="abs fsocial" style="left:608px"></div>
  <div class="abs bottom-strip"></div>
</footer>

</body>
</html>
```